Employment Agency Website Design

We are working with an employment agency in California.

Some sites to use for content/competitors and inspiration:

https://www.pinecrestjobs.com/us/en
https://www.velmorusa.com
https://www.dravenworks.us
https://www.quillora.com/en
https://www.tomvalusa.com
https://www.fernstaffing.com

Thank you for taking the time to consider designing a website for us. We are web developers based in Stockton, CA, USA. Most of our projects go through the same process. Understanding this process may help you win a project with us. We custom-code all of our websites in-house. We don’t have any requirements as to what tools you use for your design, but we prefer Figma files. For any design that we label as four-stars, we send it to the client for review. The client picks the final design they want us to use. Once we complete this process, we will continue to show additional clients all the four-star sites and purchase them later. Your designs will have multiple chances to sell. For better chances of success, we ask that you follow these guidelines.

IMAGES:
If you use any images or icons in the design, we ask that you have a link to the asset so we can purchase the image/icon. Most of the designs we submit do not have the customer’s images on them unless they have some great images. Be creative; show us the feeling you are trying to portray with your image choices. Use any royalty-free site you choose. We subscribe to Adobe and mainly use their images, but we can purchase images outside of Adobe. PLEASE NOTE: we will not submit designs to clients with watermarks on the images.

FONTS:
We ask that you identify the fonts used in the design. This can be done in a message if you want. We typically use Google Fonts and Adobe Fonts.

CONTENT:
We're always open to different content and ideas. We often submit designs with stock images so the client can see our vision. We typically take pictures after the website launch to use their images with our vision. Lorem Ipsum is fine for paragraphs, but we ask that you write the headers in correct English. We want to be able to show the vision and identify the sections of the website.

INSPIRATION:
We typically add a couple of links in the brief of websites we like to help you get started in your design.

REVISIONS:
We do not often ask for revisions of the designs unless we see something in the design that may not appeal to the client. If there are slight changes that we want to make, we do that in the development process.

FEEDBACK:
We rarely give feedback on designs during the design process. We are working on many website projects and do not have the time to provide feedback. We usually respond if your request is well thought out and asks specific questions, but a note asking “feedback, please” usually goes unanswered.

```html
<!DOCTYPE html>
<html lang="en">
<head>
<meta charset="utf-8">
<title>Stridewell Talent — The Future of Work</title>
<link href="https://fonts.googleapis.com/css2?family=Montserrat:wght@400;500;600;700&display=swap" rel="stylesheet">
<style>
:root{
  --red:#c4202f;
  --red-dark:#a51824;
  --red-deep:#8f1420;
  --ink:#1c1c1c;
  --text:#2b2b2b;
  --white:#ffffff;
  --black:#0c0c0c;
  --line:#d9d9d9;
}
*{box-sizing:border-box;margin:0;padding:0}
html,body{width:1200px;height:4934px;overflow:hidden}
body{position:relative;background:var(--white);font-family:'Montserrat',sans-serif;color:var(--text)}
.abs{position:absolute}
a{color:inherit;text-decoration:none}

/* top bar */
.topbar{left:0;top:0;width:1200px;height:40px}
.topbar .band{position:absolute;left:0;top:0}
.topbar .item{position:absolute;top:12px;color:var(--white);font-size:14px;font-weight:500;display:flex;align-items:center;gap:10px;white-space:nowrap}

/* header */
.brand{display:flex;align-items:center;gap:10px;font-weight:600;color:var(--ink)}
.brand .mark{width:34px;height:34px;background:var(--red)}
.header-brand{left:112px;top:24px;flex-direction:column;gap:4px;align-items:center}
.header-brand .mark{width:48px;height:48px}
.header-brand .name{font-size:22px;color:var(--ink)}
.header-brand .tag{font-size:9px;font-weight:400;color:var(--red);margin-top:-4px}
.nav{left:441px;top:86px;display:flex;gap:52px;font-size:14px;font-weight:600;color:var(--ink)}
.nav .active{color:var(--red)}

/* photo placeholders */
.hero-photo{left:0;top:138px;width:1200px;height:690px;
  background:
    radial-gradient(ellipse 220px 300px at 430px 330px,rgba(150,110,90,.85),rgba(150,110,90,0) 70%),
    radial-gradient(ellipse 300px 260px at 430px 620px,rgba(110,115,120,.9),rgba(110,115,120,0) 75%),
    radial-gradient(ellipse 260px 420px at 1080px 450px,rgba(240,240,240,1),rgba(240,240,240,0) 70%),
    linear-gradient(100deg,#3f3d3b 0%,#6b655f 18%,#9c958d 38%,#cfcac4 62%,#e8e6e2 100%)}
.hero-title{left:736px;top:262px;font-size:36px;font-weight:500;line-height:66px;color:var(--ink);letter-spacing:.5px}
.hero-title .red{color:var(--red)}
.hero-cut{left:0;top:700px}

/* section headings */
.sec-head{left:0;width:1200px;text-align:center;font-size:33px;font-weight:600;color:var(--ink);letter-spacing:.5px}
.sec-head .red{color:var(--red)}
.divider{display:flex;align-items:center;gap:12px;justify-content:center}
.divider .rule{width:40px;height:2px;background:var(--line)}
.divider .dot{width:16px;height:16px;background:var(--red);border-radius:50%}
.divider.light .rule{background:rgba(255,255,255,.5)}
.divider.light .dot{background:var(--white)}

/* services */
.service{width:320px;height:276px;overflow:hidden}
.service .photo{position:absolute;inset:0}
.service .label{position:absolute;left:0;bottom:0;width:300px;height:38px;background:var(--white);display:flex;align-items:center;justify-content:space-between;padding:0 18px 0 14px;font-size:16px;font-weight:600;color:var(--red)}
.service .label .plus{font-size:24px;font-weight:500}
.service.featured .photo{background:linear-gradient(160deg,#c84551,#b71f2d)}
.service.featured .body{position:absolute;inset:0;padding:62px 16px 0;text-align:center;color:var(--white)}
.service.featured h3{font-size:16px;font-weight:500;letter-spacing:.4px;margin-bottom:14px}
.service.featured p{font-size:13px;line-height:29px}
.service.featured .more{display:inline-block;margin-top:10px;font-size:13px;text-decoration:underline}

/* buttons */
.btn{height:48px;display:flex;align-items:center;justify-content:center;color:var(--white);font-size:20px;font-weight:600;letter-spacing:.3px;background:var(--red);clip-path:polygon(18px 0,100% 0,100% 100%,0 100%)}
.btn.outline{background:var(--white);color:var(--red)}

/* about */
.about-photo{left:0;top:1798px;width:632px;height:572px}
.about-title{left:675px;top:1852px;font-size:33px;font-weight:600;color:var(--ink);white-space:nowrap}
.about-title .red{color:var(--red)}
.about-text{left:675px;top:1960px;width:425px;font-size:15px;line-height:34.4px;color:var(--text)}

/* how it works */
.how{left:0;top:2463px;width:1200px;height:606px;
  background:
    linear-gradient(35deg,rgba(0,0,0,.08) 0 25%,rgba(255,255,255,0) 25% 55%,rgba(0,0,0,.06) 55% 75%,rgba(255,255,255,0) 75%),
    linear-gradient(135deg,#b51c2a 0%,#cf2a38 45%,#b01a27 100%)}
.how-head{top:2524px;color:var(--white)}
.step{background:var(--white);display:flex;align-items:center;font-size:17px;font-weight:500;color:var(--ink);line-height:33px;letter-spacing:.3px}

/* blogs */
.blog-photo{width:307px;height:236px}
.blog-card{background:var(--white);box-shadow:0 2px 10px rgba(0,0,0,.18);padding:26px 26px 0}
.blog-card .date{font-size:21px;font-weight:500;color:var(--red);margin-bottom:12px}
.blog-card p{font-size:15.5px;line-height:34px;color:var(--text)}
.blog-card.featured{background:var(--red)}
.blog-card.featured .date,.blog-card.featured p{color:var(--white)}

/* contact */
.contact-photo{left:0;top:3890px;width:1200px;height:640px;
  background:
    radial-gradient(ellipse 200px 240px at 990px 200px,rgba(170,125,100,.9),rgba(170,125,100,0) 70%),
    radial-gradient(ellipse 320px 260px at 960px 470px,rgba(70,80,95,.95),rgba(70,80,95,0) 75%),
    radial-gradient(ellipse 160px 300px at 690px 350px,rgba(40,45,55,.9),rgba(40,45,55,0) 75%),
    linear-gradient(100deg,#2f3238 0%,#5c6168 40%,#a6a8ab 75%,#d8d6d2 100%)}
.contact-red{left:0;top:3930px;width:800px;height:600px;background:var(--red);clip-path:polygon(0 0,585px 0,767px 540px,0 565px)}
.contact-head{left:0;top:3955px;width:617px;text-align:center;color:var(--white);font-size:33px;font-weight:600}
.field{background:var(--white);font-size:14px;font-weight:500;color:var(--ink);padding:15px 16px}

/* footer */
.footer{left:0;width:1200px;background:var(--black)}
.footer-brand{left:0;top:4556px;width:1200px;justify-content:center;color:var(--white);font-size:44px;font-weight:500}
.footer-brand .mark{width:44px;height:44px;background:var(--white)}
.footer-tag{left:497px;top:4617px;color:var(--white);font-size:16px;font-weight:400}
.foot-list{color:var(--white);font-size:15px;font-weight:600;line-height:40px}
.foot-contact{left:70px;top:4717px;color:var(--white);font-size:14px;font-weight:600;line-height:38px}
.foot-contact .row{display:flex;gap:26px;align-items:flex-start}
.foot-contact .ico{width:20px;padding-top:9px}
.socials{left:976px;top:4718px;display:flex;gap:8px}
.socials span{width:32px;height:32px;border:2px solid var(--white);border-radius:50%}
.copy{left:976px;top:4778px;color:var(--white);font-size:14px;font-weight:600;line-height:34px}
</style>
</head>
<body>

<!-- top bar -->
<div class="abs topbar">
  <svg class="band" width="1200" height="40" aria-hidden="true"><polygon points="392,0 1200,0 1200,40 420,40" fill="var(--red)"/></svg>
  <div class="item" style="left:526px">
    <svg width="16" height="12" viewBox="0 0 16 12" aria-hidden="true"><rect x="1" y="1" width="14" height="10" fill="none" stroke="#fff" stroke-width="1.6"/><polyline points="1,1 8,7 15,1" fill="none" stroke="#fff" stroke-width="1.6"/></svg>
    <span>HELLO@STRIDEWELLTALENT.COM</span>
  </div>
  <div class="item" style="left:920px">
    <svg width="14" height="14" viewBox="0 0 24 24" aria-hidden="true"><path d="M6.6 10.8a15 15 0 0 0 6.6 6.6l2.2-2.2c.3-.3.7-.4 1-.2 1.1.4 2.3.6 3.6.6.6 0 1 .4 1 1V20c0 .6-.4 1-1 1A17 17 0 0 1 3 4c0-.6.4-1 1-1h3.5c.6 0 1 .4 1 1 0 1.3.2 2.5.6 3.6.1.3 0 .7-.2 1z" fill="#fff"/></svg>
    <span>+1 555 014 2290</span>
  </div>
</div>

<!-- header -->
<div class="abs brand header-brand">
  <span class="mark"></span>
  <span class="name">stridewelltalent</span>
  <span class="tag">The future of work.</span>
</div>
<nav class="abs nav">
  <a class="active">HOME</a><a>ABOUT US</a><a>OUR SERVICES</a><a>LATEST BLOGS</a><a>CONTACT US</a>
</nav>

<!-- hero -->
<div class="abs hero-photo" role="img" aria-label="Photo of a recruiter at a computer in a bright office"></div>
<h1 class="abs hero-title">WELCOME TO<br><span class="red">STRIDEWELL TALENT</span><br><span class="red">THE FUTURE OF WORK</span></h1>
<svg class="abs hero-cut" width="1200" height="130" aria-hidden="true">
  <polygon points="0,38 600,124 1200,38 1200,130 0,130" fill="var(--red)"/>
  <polygon points="0,52 600,124 1200,52 1200,130 0,130" fill="#fff"/>
</svg>

<!-- services -->
<h2 class="abs sec-head" style="top:908px"><span class="red">OUR</span> SERVICES</h2>
<div class="abs divider" style="left:0;top:964px;width:1200px"><span class="rule"></span><span class="dot"></span><span class="rule"></span></div>

<div class="abs service" style="left:111px;top:1041px">
  <div class="photo" role="img" aria-label="Photo of colleagues shaking hands in an office" style="background:radial-gradient(ellipse 90px 120px at 150px 130px,rgba(190,150,120,.7),rgba(190,150,120,0)),linear-gradient(150deg,#d8dcdf,#7d8287)"></div>
  <div class="label">TEMPORARY STAFFING <span class="plus">+</span></div>
</div>
<div class="abs service featured" style="left:441px;top:1041px">
  <div class="photo" role="img" aria-label="Photo of payroll paperwork under a red overlay"></div>
  <div class="body">
    <h3>PAYROLL SERVICES</h3>
    <p>Lorem ipsum dolor sit amet, consectetur adipiscing elit, sed do eiusmod tempor incididunt ut labore et.</p>
    <a class="more">LEARN MORE</a>
  </div>
</div>
<div class="abs service" style="left:769px;top:1041px">
  <div class="photo" role="img" aria-label="Photo of a hand using a phone with digital overlays" style="background:radial-gradient(ellipse 110px 110px at 160px 140px,rgba(220,210,200,.7),rgba(220,210,200,0)),linear-gradient(150deg,#b9a999,#4b4744)"></div>
  <div class="label">TECHNOLOGY <span class="plus">+</span></div>
</div>
<div class="abs service" style="left:111px;top:1330px">
  <div class="photo" role="img" aria-label="Photo of a smiling businessman shaking hands" style="background:radial-gradient(ellipse 80px 140px at 210px 150px,rgba(60,60,65,.85),rgba(60,60,65,0)),linear-gradient(150deg,#a6a4a1,#4e4e50)"></div>
  <div class="label">DIRECT PLACEMENT <span class="plus">+</span></div>
</div>
<div class="abs service" style="left:441px;top:1330px">
  <div class="photo" role="img" aria-label="Photo of a telecom tower against a dusk sky" style="background:linear-gradient(180deg,#5a7bc4,#9c8fc8 60%,#e5a98e)"></div>
  <div class="label">TELECOM <span class="plus">+</span></div>
</div>
<div class="abs service" style="left:769px;top:1330px">
  <div class="photo" role="img" aria-label="Photo of hands typing with finance charts overlay" style="background:radial-gradient(ellipse 120px 90px at 180px 170px,rgba(80,180,170,.55),rgba(80,180,170,0)),linear-gradient(150deg,#a7b7a2,#2c3835)"></div>
  <div class="label">ACCOUNTING <span class="plus">+</span></div>
</div>

<a class="abs btn" style="left:470px;top:1662px;width:262px">VIEW ALL SERVICES</a>

<!-- about -->
<div class="abs about-photo">
  <svg width="632" height="572" aria-hidden="true">
    <polygon points="416,56 440,56 632,572 608,572" fill="var(--red)"/>
  </svg>
  <div class="abs" role="img" aria-label="Photo of a businessman reading a document at his laptop" style="left:0;top:0;width:612px;height:572px;clip-path:polygon(0 0,230px 0,240px 56px,416px 56px,608px 572px,0 572px);
    background:
      radial-gradient(ellipse 110px 130px at 200px 130px,rgba(185,140,115,.9),rgba(185,140,115,0) 70%),
      radial-gradient(ellipse 240px 220px at 210px 400px,rgba(75,80,92,.95),rgba(75,80,92,0) 75%),
      radial-gradient(ellipse 120px 90px at 480px 470px,rgba(235,235,232,.95),rgba(235,235,232,0) 75%),
      linear-gradient(120deg,#3a3c40,#807e7a 45%,#c6c2bc 80%)"></div>
</div>
<h2 class="abs about-title"><span class="red">ABOUT</span> STRIDEWELL TALENT</h2>
<div class="abs divider" style="left:695px;top:1910px"><span class="rule"></span><span class="dot"></span><span class="rule"></span></div>
<p class="abs about-text">Sed ut perspiciatis unde omnis iste natus error sit voluptatem accusantium doloremque laudantium, totam rem aperiam, eaque ipsa quae ab illo inventore veritatis et quasi architecto beatae vitae dicta sunt explicabo. Nemo enim ipsam voluptatem quia voluptas sit aspernatur aut odit aut fugit, sed quia consequuntur magni dolores eos qui ratione voluptatem sequi nesciunt. Neque porro quisquam est.</p>
<a class="abs btn" style="left:677px;top:2306px;width:205px">LEARN MORE</a>

<!-- how it works -->
<div class="abs how" role="img" aria-label="Red low-poly geometric background"></div>
<h2 class="abs sec-head how-head">HOW IT WORKS</h2>
<div class="abs divider light" style="left:0;top:2581px;width:1200px"><span class="rule"></span><span class="dot"></span><span class="rule"></span></div>

<svg class="abs" style="left:270px;top:2660px" width="680" height="350" aria-hidden="true">
  <g fill="#b01b28">
    <polygon points="320,60 350,2 485,2 485,118 350,118"/>
    <polygon points="300,172 345,100 380,100 420,172 380,244 345,244"/>
    <polygon points="320,270 350,212 485,212 485,328 350,328"/>
  </g>
</svg>
<div class="abs step" style="left:617px;top:2690px;width:313px;height:107px;padding-left:90px;clip-path:polygon(26px 0,100% 0,100% 100%,26px 100%,0 50%)">DESCRIBE YOUR NEED</div>
<div class="abs step" style="left:270px;top:2778px;width:315px;height:109px;padding-right:119px;justify-content:flex-end;text-align:right;clip-path:polygon(0 0,289px 0,100% 50%,289px 100%,0 100%)"><span>CONNECT WITH A<br>RECRUITE</span></div>
<div class="abs step" style="left:617px;top:2875px;width:313px;height:108px;padding-left:115px;clip-path:polygon(26px 0,100% 0,100% 100%,26px 100%,0 50%)">VIEW MATCHING<br>CANDIDATES</div>

<!-- step icons -->
<svg class="abs" style="left:648px;top:2722px" width="46" height="44" viewBox="0 0 46 44" aria-hidden="true" fill="none" stroke="var(--red)" stroke-width="2">
  <rect x="12" y="2" width="32" height="24"/><line x1="18" y1="10" x2="38" y2="10"/><line x1="18" y1="17" x2="32" y2="17"/>
  <circle cx="8" cy="20" r="5"/><path d="M1 42V33c0-4 3-6 7-6s7 2 7 6v9"/>
</svg>
<svg class="abs" style="left:490px;top:2810px" width="52" height="48" viewBox="0 0 52 48" aria-hidden="true" fill="none" stroke="var(--red)" stroke-width="2">
  <circle cx="10" cy="10" r="8"/><circle cx="40" cy="12" r="8"/><circle cx="22" cy="36" r="9"/><line x1="18" y1="10" x2="32" y2="12"/><line x1="14" y1="17" x2="19" y2="27"/><line x1="35" y1="19" x2="29" y2="29"/><line x1="29" y1="42" x2="36" y2="46"/>
</svg>
<svg class="abs" style="left:660px;top:2906px" width="44" height="46" viewBox="0 0 44 46" aria-hidden="true" fill="none" stroke="var(--red)" stroke-width="2">
  <path d="M4 2h22l8 8v14"/><path d="M4 2v40h18"/><line x1="9" y1="14" x2="24" y2="14"/><line x1="9" y1="21" x2="20" y2="21"/>
  <circle cx="30" cy="32" r="8"/><line x1="36" y1="38" x2="42" y2="44"/>
</svg>

<!-- blogs -->
<h2 class="abs sec-head" style="top:3154px"><span class="red">LATEST</span> BLOGS</h2>
<div class="abs divider" style="left:0;top:3212px;width:1200px"><span class="rule"></span><span class="dot"></span><span class="rule"></span></div>

<div class="abs blog-photo" role="img" aria-label="Photo of a team reviewing documents together" style="left:111px;top:3303px;background:radial-gradient(ellipse 140px 90px at 150px 120px,rgba(170,120,90,.75),rgba(170,120,90,0)),linear-gradient(150deg,#d6d1c9,#5f5852)"></div>
<div class="abs blog-card" style="left:126px;top:3450px;width:279px;height:213px;clip-path:polygon(0 40px,279px 0,279px 100%,0 100%);padding-top:60px">
  <div class="date">01 JAN 2024</div>
  <p>Lorem ipsum dolor sit amet, consectetur adipiscing elit,</p>
</div>

<div class="abs blog-photo" role="img" aria-label="Photo of a hand signing papers on a desk" style="left:447px;top:3303px;background:radial-gradient(ellipse 90px 60px at 100px 170px,rgba(90,80,75,.55),rgba(90,80,75,0)),linear-gradient(150deg,#eeeeec,#b3b4b3)"></div>
<div class="abs blog-card featured" style="left:462px;top:3450px;width:278px;height:282px;clip-path:polygon(0 40px,278px 0,278px 100%,0 100%);padding-top:60px">
  <div class="date">21 JAN 2024</div>
  <p>Lorem ipsum dolor sit amet, consectetur adipiscing elit, sed do eiusmod tempor incididunt ut labore et</p>
</div>

<div class="abs blog-photo" role="img" aria-label="Photo of a smiling professional at her desk" style="left:782px;top:3303px;background:radial-gradient(ellipse 70px 110px at 160px 110px,rgba(235,235,235,.85),rgba(235,235,235,0)),linear-gradient(150deg,#8f8c88,#46433f)"></div>
<div class="abs blog-card" style="left:797px;top:3450px;width:279px;height:213px;clip-path:polygon(0 40px,279px 0,279px 100%,0 100%);padding-top:60px">
  <div class="date">01 FEB 2024</div>
  <p>Lorem ipsum dolor sit amet, consectetur adipiscing elit,</p>
</div>

<a class="abs btn" style="left:493px;top:3769px;width:218px">VIEW ALL BLOGS</a>

<!-- contact -->
<div class="abs contact-photo" role="img" aria-label="Photo of a smiling recruiter talking with a candidate" style="clip-path:polygon(585px 40px,1200px 40px,1200px 640px,0 640px)"></div>
<div class="abs contact-red"></div>
<h2 class="abs contact-head">CONTACT US</h2>
<div class="abs divider light" style="left:0;top:4012px;width:617px"><span class="rule"></span><span class="dot"></span><span class="rule"></span></div>
<div class="abs field" style="left:73px;top:4070px;width:228px;height:46px">FIRST NAME</div>
<div class="abs field" style="left:314px;top:4070px;width:230px;height:46px">LAST NAME</div>
<div class="abs field" style="left:73px;top:4135px;width:228px;height:46px">EMAIL ADDRESS</div>
<div class="abs field" style="left:314px;top:4135px;width:230px;height:46px">MOBILE NUMBER</div>
<div class="abs field" style="left:73px;top:4198px;width:471px;height:90px">MESSAGE</div>
<a class="abs btn outline" style="left:197px;top:4327px;width:227px;height:57px;font-size:22px">SUBMIT NOW</a>

<!-- footer -->
<footer class="abs footer" style="top:4505px;height:429px"></footer>
<svg class="abs" style="left:0;top:4450px" width="1200" height="60" aria-hidden="true">
  <polygon points="0,48 600,0 1200,48 1200,60 0,60" fill="var(--black)"/>
  <polyline points="0,40 600,-6 1200,40" fill="none" stroke="#fff" stroke-width="6"/>
</svg>

<div class="abs brand footer-brand"><span class="mark"></span><span>stridewelltalent</span></div>
<div class="abs footer-tag">The future of work.</div>

<div class="abs foot-contact">
  <div class="row"><span class="ico"><svg width="16" height="16" viewBox="0 0 24 24" aria-hidden="true"><path d="M6.6 10.8a15 15 0 0 0 6.6 6.6l2.2-2.2c.3-.3.7-.4 1-.2 1.1.4 2.3.6 3.6.6.6 0 1 .4 1 1V20c0 .6-.4 1-1 1A17 17 0 0 1 3 4c0-.6.4-1 1-1h3.5c.6 0 1 .4 1 1 0 1.3.2 2.5.6 3.6.1.3 0 .7-.2 1z" fill="#fff"/></svg></span><span>+1 555 014 2290</span></div>
  <div class="row"><span class="ico"><svg width="18" height="22" viewBox="0 0 18 22" aria-hidden="true"><path d="M9 1a7 7 0 0 0-7 7c0 5 7 12 7 12s7-7 7-12a7 7 0 0 0-7-7z" fill="none" stroke="#fff" stroke-width="2"/><circle cx="9" cy="8" r="2.5" fill="#fff"/></svg></span><span>12, STRIDEWELL LANE LOREM<br>IPSUM AMET SIT<br>098 762</span></div>
</div>
<svg class="abs" style="left:340px;top:4720px" width="80" height="170" aria-hidden="true"><line x1="74" y1="2" x2="6" y2="168" stroke="#fff" stroke-width="1.5"/></svg>
<div class="abs foot-list" style="left:447px;top:4718px">HOME<br>OUR SERVICES<br>WHY CHOOSE US</div>
<div class="abs foot-list" style="left:690px;top:4718px">ABOUT US<br>LATEST BLOGS<br>CONTACT US</div>
<svg class="abs" style="left:870px;top:4720px" width="80" height="170" aria-hidden="true"><line x1="74" y1="2" x2="6" y2="168" stroke="#fff" stroke-width="1.5"/></svg>
<div class="abs socials" aria-label="Social links"><span></span><span></span><span></span></div>
<div class="abs copy">@2024 COPYRIGHTS.<br>ALL RIGHTS RESERVED.</div>

</body>
</html>
```